Business Cards - New Logo Rebranding

Hello We know have a red and blue logo and are looking to create new cards. We are looking for the best creativity of the new logo merged with some of the existing artwork provided.

Target Market(s)

Realtors

Industry/Entity Type

Real Estate

Contact Information for Business Card

New logo with rebranded colors

Requirements
Must have
• Creative use of the new logo

```html
<!DOCTYPE html>
<html lang="en">
<head>
<meta charset="utf-8">
<title>Keystone Group Business Card</title>
<link href="https://fonts.googleapis.com/css2?family=Lexend:wght@400;500;600;700&display=swap" rel="stylesheet">
<style>
  :root {
    --brand-red: #d0323c;
    --brand-blue: #1466ad;
    --ink: #1f1f24;
    --paper: #f3f3f5;
    --stage: #dcdcde;
    --white: #ffffff;
    --soft-blue: #a9c6e2;
    --soft-red: #f0c3c6;
  }
  * { box-sizing: border-box; margin: 0; padding: 0; }
  html, body { width: 1200px; height: 928px; overflow: hidden; }
  body { background: var(--stage); font-family: "Lexend", sans-serif; position: relative; }

  .card {
    position: absolute; top: 68px; width: 415px; height: 725px;
    background: var(--paper); overflow: hidden;
  }
  .card--front { left: 94px; }
  .card--back { left: 652px; }
  .card svg.shape { position: absolute; left: 0; top: 0; }

  /* front */
  .brand-mark {
    position: absolute; left: 166px; top: 18px; width: 70px; height: 70px;
    border-radius: 50%; background: var(--brand-blue);
  }
  .brand-name {
    position: absolute; left: 0; width: 373px; top: 108px; text-align: center;
    font-weight: 700; font-size: 25px; letter-spacing: 1px; color: var(--brand-blue);
  }
  .brand-tagline {
    position: absolute; left: 0; width: 373px; top: 165px; text-align: center;
    font-weight: 700; font-size: 9px; letter-spacing: .3px; color: var(--brand-blue);
  }
  .portrait {
    position: absolute; left: 57px; top: 188px; width: 290px; height: 290px; border-radius: 50%;
    background: radial-gradient(circle at 50% 40%, var(--soft-blue) 0%, #7fa6cf 55%, var(--soft-red) 100%);
  }
  .name-plate {
    position: absolute; left: 61px; top: 446px; width: 294px; height: 59px;
    background: var(--brand-red); border-radius: 30px 30px 40px 40px;
    color: var(--white); text-align: center; padding-top: 6px;
  }
  .name-plate__name { font-weight: 700; font-size: 24px; letter-spacing: .5px; line-height: 1.1; }
  .name-plate__role { font-weight: 400; font-size: 15px; line-height: 1.3; }

  .contact { position: absolute; left: 22px; display: flex; align-items: center; color: var(--white); font-weight: 500; }
  .contact__icon {
    width: 32px; height: 32px; border-radius: 50%; background: var(--white);
    display: flex; align-items: center; justify-content: center; margin-right: 14px; flex: none;
  }
  .contact--phone { top: 537px; font-size: 16px; line-height: 26px; }
  .contact--web { top: 612px; font-size: 18px; }
  .contact--mail { top: 664px; font-size: 15.5px; }

  .service-strip {
    position: absolute; left: 373px; top: 0; width: 42px; height: 725px;
    background: var(--brand-red); border-radius: 24px 0 0 24px;
  }
  .service-strip__text {
    position: absolute; left: 21px; top: 365px; transform: translate(-50%, -50%) rotate(-90deg);
    white-space: nowrap; color: var(--white); font-weight: 500; font-size: 19px; letter-spacing: 1px;
  }

  /* back */
  .why-title {
    position: absolute; left: 31px; top: 36px; font-weight: 600; font-size: 22px; color: var(--brand-red); white-space: nowrap;
  }
  .why-list { list-style: none; position: absolute; left: 48px; top: 78px; width: 350px; }
  .why-list li {
    position: relative; padding-left: 30px; font-size: 16.5px; line-height: 22px; color: var(--ink); margin-bottom: 12px;
  }
  .why-list li::before {
    content: ""; position: absolute; left: 0; top: 3px; width: 20px; height: 20px; border-radius: 50%;
    background: var(--brand-blue); box-shadow: inset 0 0 0 3px var(--soft-blue);
  }
  .banner {
    position: absolute; left: 38px; top: 421px; width: 319px; height: 67px;
    background: var(--brand-red); border-radius: 30px 30px 40px 40px;
    color: var(--white); text-align: center; font-weight: 500; font-size: 19.5px; line-height: 28px; padding-top: 6px;
  }
  .badge { position: absolute; border-radius: 50%; }
  .badge--heroes { left: 44px; top: 530px; width: 80px; height: 80px; background: #b93040; box-shadow: inset 0 0 0 8px #e4e4ec; }
  .badge--master { left: 162px; top: 530px; width: 80px; height: 80px; background: #3b4a6a; box-shadow: inset 0 0 0 8px #d8b23a; }
  .badge--cpi { left: 277px; top: 530px; width: 80px; height: 80px; background: #2a2a2a; box-shadow: inset 0 0 0 8px #c9b98a; }
  .badge--drone-seal { left: 29px; top: 638px; width: 66px; height: 66px; background: #2e6b3a; box-shadow: inset 0 0 0 6px #d2b24a; }
  .badge--drone-plate { position: absolute; left: 90px; top: 647px; width: 80px; height: 48px; background: #23306a; border: 2px solid #d2b24a; }
  .badge--infrared { left: 201px; top: 640px; width: 46px; height: 46px; background: transparent; border: 8px solid #f0f0f0; }
  .badge--reviews { position: absolute; left: 283px; top: 646px; width: 96px; height: 46px; background: var(--white); border-radius: 6px; }
</style>
</head>
<body>

<article class="card card--front">
  <div class="brand-mark"></div>
  <div class="brand-name">KEYSTONE GROUP</div>
  <div class="brand-tagline">INSPECTION PROFESSIONALS</div>

  <div class="portrait" role="img" aria-label="Portrait photo of the inspector in a blue company polo, set in a round badge frame"></div>

  <svg class="shape" width="415" height="725" viewBox="0 0 415 725" aria-hidden="true">
    <path d="M0,455 Q30,448 48,478 L70,510 Q86,530 115,530 L300,530 Q328,530 345,508 L373,470 V725 H0 Z" fill="var(--brand-blue)"/>
  </svg>

  <div class="name-plate">
    <div class="name-plate__name">DAN MORELAND</div>
    <div class="name-plate__role">Certified Mold Inspector</div>
  </div>

  <div class="contact contact--phone">
    <span class="contact__icon">
      <svg width="14" height="18" viewBox="0 0 14 18"><rect x="2" y="1" width="10" height="16" rx="2" fill="none" stroke="var(--brand-red)" stroke-width="2"/></svg>
    </span>
    <span>800.555.0142,<br>562.555.0187</span>
  </div>
  <div class="contact contact--web">
    <span class="contact__icon">
      <svg width="18" height="18" viewBox="0 0 18 18"><g fill="none" stroke="var(--brand-red)" stroke-width="2"><rect x="1" y="7" width="9" height="5" rx="2.5" transform="rotate(-45 5.5 9.5)"/><rect x="8" y="6" width="9" height="5" rx="2.5" transform="rotate(-45 12.5 8.5)"/></g></svg>
    </span>
    <span>www.KeystoneInspect.com</span>
  </div>
  <div class="contact contact--mail">
    <span class="contact__icon">
      <svg width="18" height="14" viewBox="0 0 18 14"><g fill="none" stroke="var(--brand-red)" stroke-width="2"><rect x="1" y="1" width="16" height="12" rx="1"/><path d="M1,2 L9,8 L17,2"/></g></svg>
    </span>
    <span>danmoreland@keystoneinspect.com</span>
  </div>

  <div class="service-strip">
    <div class="service-strip__text">HOME · SEWER · MOLD · COMMERCIAL · TERMITE · ROOF</div>
  </div>
</article>

<article class="card card--back">
  <h2 class="why-title">Why Choose the Keystone Group...</h2>
  <ul class="why-list">
    <li>Performing Inspections Since 1984</li>
    <li>HomeCert Certified Master<br>/ Professional Inspectors®</li>
    <li>500,000+ Inspections<br>Completed Statewide</li>
    <li>Request of Repairs Pricer Report</li>
    <li>90-Day Inspection Guarantees</li>
    <li>FDLA Drone Licensed Roof<br>Inspectors upon request</li>
    <li>5,000+ 5-Star Reviews on<br>Revuo &amp; Starly</li>
  </ul>

  <svg class="shape" width="415" height="725" viewBox="0 0 415 725" aria-hidden="true">
    <path d="M0,429 Q30,424 46,455 L68,492 Q84,512 112,512 L303,512 Q331,512 347,492 L369,455 Q385,424 415,429 V725 H0 Z" fill="var(--brand-blue)"/>
  </svg>

  <div class="banner">CALIFORNIA'S #1<br>INSPECTION COMPANY!</div>

  <div class="badge badge--heroes"></div>
  <div class="badge badge--master"></div>
  <div class="badge badge--cpi"></div>
  <div class="badge--drone-plate"></div>
  <div class="badge badge--drone-seal"></div>
  <div class="badge badge--infrared"></div>
  <div class="badge--reviews"></div>
</article>

</body>
</html>
```